A clean crisp business card for a Landscape Construction company. Designed to be easy to read contact/ info and also be appealing/interesting, unlike a traditional business card.

Industry/Entity Type

Landscape Construction

Contact Information for Business Card

Company name : Brambleford Landscape Construction, phone number: (877) 62Vista, website:Bramblefordyards.example, Email, sales@bramblefordyards.example

Requirements
Nice to have
• Luxurious finishes/ details…. Icons or emblems next to contact info
Should not have
• Clipart or general pictures

```html
<!DOCTYPE html>
<html lang="en">
<head>
<meta charset="utf-8">
<title>Brambleford Landscape Construction – Business Card</title>
<link rel="stylesheet" href="https://fonts.googleapis.com/css2?family=Cinzel:wght@400;600&family=Arimo:wght@400&display=swap">
<style>
  :root {
    --page: #3a302b;
    --card-black: #0b0b0b;
    --card-edge: #1c1c1c;
    --brand-blue: #2f7fd6;
    --brand-green: #9ccc2a;
    --text-light: #f2f2f2;
  }
  html, body {
    margin: 0;
    width: 1200px;
    height: 716px;
    overflow: hidden;
    background: var(--page);
  }
  .stage {
    width: 1200px;
    height: 716px;
    display: flex;
    align-items: center;
    justify-content: center;
    gap: 40px;
  }
  .card {
    position: relative;
    width: 540px;
    height: 309px;
    background: radial-gradient(ellipse at 30% 20%, var(--card-edge), var(--card-black) 70%);
    overflow: hidden;
    box-shadow: 0 12px 30px rgba(0,0,0,.55);
  }
  .wordmark {
    display: flex;
    align-items: center;
    gap: 12px;
    font-family: "Cinzel", serif;
    font-weight: 600;
    color: var(--brand-blue);
    line-height: 1.1;
  }
  .wordmark__dot {
    flex: none;
    border-radius: 50%;
    background: var(--brand-blue);
  }
  .card--front .wordmark {
    position: absolute;
    left: 50%;
    top: 50%;
    transform: translate(-50%, -50%);
    font-size: 30px;
  }
  .card--front .wordmark__dot { width: 30px; height: 30px; }
  .wordmark__sub { display: block; font-size: .5em; letter-spacing: .2em; }

  .card--back .wordmark {
    position: absolute;
    left: 32px;
    top: 36px;
    font-size: 24px;
  }
  .card--back .wordmark__dot { width: 24px; height: 24px; }

  .holder {
    position: absolute;
    right: 34px;
    top: 138px;
    text-align: right;
    font-family: "Cinzel", serif;
  }
  .holder__name {
    margin: 0;
    font-size: 24px;
    font-weight: 400;
    color: var(--brand-blue);
    letter-spacing: .04em;
  }
  .holder__role {
    margin: 2px 0 0;
    font-size: 15px;
    color: var(--brand-green);
    letter-spacing: .08em;
  }
  .rule {
    position: absolute;
    left: 32px;
    right: 34px;
    top: 196px;
    height: 1px;
    background: var(--brand-green);
  }
  .accent-tab {
    position: absolute;
    right: 0;
    top: 150px;
    width: 8px;
    height: 40px;
    background: var(--brand-green);
  }
  .contacts {
    position: absolute;
    left: 32px;
    top: 206px;
    margin: 0;
    padding: 0;
    list-style: none;
    font-family: "Arimo", sans-serif;
    font-size: 12.5px;
    color: var(--text-light);
  }
  .contacts li {
    display: flex;
    align-items: center;
    gap: 8px;
    height: 17px;
  }
  .contacts svg { width: 11px; height: 11px; flex: none; }
  .base-band {
    position: absolute;
    left: 0;
    bottom: 0;
    width: 540px;
    height: 60px;
  }
</style>
</head>
<body>
<main class="stage">

  <section class="card card--front" aria-label="Card front">
    <div class="wordmark">
      <span class="wordmark__dot"></span>
      <span>Brambleford<span class="wordmark__sub">Landscape Construction</span></span>
    </div>
  </section>

  <section class="card card--back" aria-label="Card back">
    <div class="wordmark">
      <span class="wordmark__dot"></span>
      <span>Brambleford<span class="wordmark__sub">Landscape Construction</span></span>
    </div>

    <div class="holder">
      <p class="holder__name">DORIAN HALE</p>
      <p class="holder__role">DIRECTOR</p>
    </div>
    <div class="rule"></div>
    <div class="accent-tab"></div>

    <ul class="contacts">
      <li>
        <svg viewBox="0 0 12 12"><path d="M3 1l2 2.5-1.2 1.3a7 7 0 0 0 3.4 3.4L8.5 7 11 9l-1 2c-5 0-9-4-9-9z" fill="#9ccc2a"/></svg>
        (877) 62Vista
      </li>
      <li>
        <svg viewBox="0 0 12 12"><rect x="1" y="2.5" width="10" height="7" fill="none" stroke="#9ccc2a"/><path d="M1 2.5l5 4 5-4" fill="none" stroke="#9ccc2a"/></svg>
        sales@bramblefordyards.example
      </li>
      <li>
        <svg viewBox="0 0 12 12"><circle cx="6" cy="6" r="5" fill="none" stroke="#9ccc2a"/><path d="M1 6h10M6 1c-3 3-3 7 0 10M6 1c3 3 3 7 0 10" fill="none" stroke="#9ccc2a" stroke-width=".8"/></svg>
        www.bramblefordyards.example
      </li>
    </ul>

    <svg class="base-band" viewBox="0 0 540 60" preserveAspectRatio="none" aria-hidden="true">
      <path d="M0 10 L250 44 Q262 46 280 44 L540 44 L540 60 L0 60 Z" fill="#2f7fd6"/>
      <path d="M0 4 L250 38 Q262 40 280 38 L300 38 L260 44 Q250 45 240 44 L0 12 Z" fill="#9ccc2a"/>
      <path d="M280 44 Q340 40 380 48 L540 48 L540 44 Z" fill="#2f7fd6"/>
    </svg>
  </section>

</main>
</body>
</html>
```